Bramblewood Card Company Business Cards

We are a trading card store with Glimmorax, sports and other TCG cards, we need a business card design that encompasses a clean cut, modern style with a retro flare. website is bramblewoodcardco.com for reference. Can utilize a comic book era feel or a more modern outdoor feel to utilize the "Pacific Northwest" elements of tress, mountains, etc.

Industry/Entity Type

Trading cards and collectibles

Contact Information for Business Card

business name, email address, phone number, name, owner job title

Font styles to use
Sans Serif

```html
<!DOCTYPE html>
<html lang="en">
<head>
<meta charset="utf-8">
<title>Bramblewood Card Company – Business Cards</title>
<link href="https://fonts.googleapis.com/css2?family=Josefin+Sans:wght@600;700&family=Arimo:wght@400;700&display=swap" rel="stylesheet">
<style>
  :root {
    --backdrop: #1b1c1e;
    --card-white: #f6f6f4;
    --brand-blue: #0ab3d8;
    --brand-blue-deep: #0891b2;
    --brand-blue-light: #3fd0ec;
    --ink-grey: #5f6062;
    --line-grey: #6a6a6a;
  }
  * { box-sizing: border-box; margin: 0; padding: 0; }
  html, body { width: 1200px; height: 963px; overflow: hidden; }
  body {
    background: var(--backdrop);
    display: flex; flex-direction: column; align-items: center; justify-content: center;
    gap: 56px;
  }
  .card {
    position: relative; width: 700px; height: 400px;
    border-radius: 30px; overflow: hidden;
  }

  /* Front */
  .card-front { background: var(--card-white); }
  .front-swoosh { position: absolute; inset: 0; }
  .front-brand {
    position: absolute; top: 96px; left: 0; right: 0; text-align: center;
    font-family: "Josefin Sans", sans-serif; font-weight: 700;
    font-size: 30px; letter-spacing: 2px; text-transform: uppercase;
    color: var(--ink-grey); white-space: nowrap;
  }
  .contact-row {
    position: absolute; top: 212px; left: 0; right: 0;
    display: flex; justify-content: center; align-items: center; gap: 22px;
  }
  .person { text-align: right; }
  .person-name {
    font-family: "Arimo", sans-serif; font-weight: 700; font-size: 24px;
    color: var(--brand-blue); text-transform: uppercase; letter-spacing: 0.5px;
    white-space: nowrap;
  }
  .person-title {
    font-family: "Arimo", sans-serif; font-size: 17px; color: var(--ink-grey);
  }
  .divider { width: 1.5px; height: 58px; background: var(--ink-grey); }
  .details { list-style: none; font-family: "Arimo", sans-serif; font-size: 17px; color: var(--ink-grey); }
  .details li { display: flex; align-items: center; gap: 10px; line-height: 1.6; white-space: nowrap; }
  .details svg { width: 16px; height: 16px; flex: none; }

  /* Back */
  .card-back { background: var(--brand-blue); }
  .back-brand {
    position: absolute; top: 92px; left: 0; right: 0; text-align: center;
    font-family: "Josefin Sans", sans-serif; font-weight: 700;
    font-size: 36px; letter-spacing: 2px; text-transform: uppercase;
    color: var(--card-white); white-space: nowrap;
  }
  .mountain-art {
    position: absolute; left: 0; right: 0; bottom: 0; height: 190px;
    background: linear-gradient(180deg, var(--brand-blue-light) 0%, var(--brand-blue) 45%, var(--brand-blue-deep) 100%);
  }
</style>
</head>
<body>
  <section class="card card-front" aria-label="Business card front">
    <svg class="front-swoosh" viewBox="0 0 700 400" preserveAspectRatio="none" aria-hidden="true">
      <path d="M0 262 Q330 360 700 392 L700 400 L0 400 Z" fill="var(--brand-blue)"/>
      <path d="M22 270 Q320 352 680 384" fill="none" stroke="var(--line-grey)" stroke-width="3"/>
    </svg>
    <p class="front-brand">Bramblewood Card Company</p>
    <div class="contact-row">
      <div class="person">
        <p class="person-name">Dorian Vale</p>
        <p class="person-title">Manager</p>
      </div>
      <span class="divider"></span>
      <ul class="details">
        <li>
          <svg viewBox="0 0 24 24"><path d="M6.6 10.8a15 15 0 0 0 6.6 6.6l2.2-2.2c.3-.3.7-.4 1-.2 1.1.4 2.3.6 3.6.6.6 0 1 .4 1 1V20c0 .6-.4 1-1 1A17 17 0 0 1 3 4c0-.6.4-1 1-1h3.5c.6 0 1 .4 1 1 0 1.3.2 2.5.6 3.6.1.3 0 .7-.2 1z" fill="var(--brand-blue)"/></svg>
          360-555-0148
        </li>
        <li>
          <svg viewBox="0 0 24 24"><rect x="2.5" y="5" width="19" height="14" rx="1.5" fill="none" stroke="var(--brand-blue)" stroke-width="2"/><path d="M3 6l9 7 9-7" fill="none" stroke="var(--brand-blue)" stroke-width="2"/></svg>
          info@bramblewoodcardco.com
        </li>
      </ul>
    </div>
  </section>

  <section class="card card-back" aria-label="Business card back">
    <p class="back-brand">Bramblewood Card Company</p>
    <div class="mountain-art" role="img" aria-label="Embossed mountain range silhouette in tonal blues"></div>
  </section>
</body>
</html>
```